Harborview Estates Business Card for Apartment Buildings

Create business cards for resident managers who run apartment buildings. The audience is the public who are searching for apartment rentals, and current residents who live at the apartment building. Key design element will be incorporating the company logo, however, the logo cannot dominate. The building name and manager name are more important than the logo. Current business card design leaves little room for copy, so we may need to reduce the size on the current card to allow for more space for copy.

Target Market(s)

Adults 18-65 years of age, who are looking for an apartment rental, plus current residents who live at our apartment buildings.

Industry/Entity Type

Property Management

Contact Information for Business Card

A major design element will be use of the company logo. Important property and manager contact information must be part of the design. The size of the logo will need to be reduced to make room for building and manager contact copy.

Font styles to use
Sans Serif

Colors
3176b5
000000
959595
ffffff

Requirements
Must have
• 1) Incorporate the company logo.
• 2) Use the company colors (dark blue, black/grey, over white).
• 3) FEATURE THE BUILDING NAME
• 4) FEATURE THE MANAGER NAME
• 5) The company name is less important than BUILDING and MANAGER
• 6) Manager contact information
• **SEE ATTACHED CREATIVE BRIEF**
Nice to have
• 1) Back of card logo watermark
• 2) Ability to write notes on back of carfd
Should not have
• Avoid letting the company logo dominate the card, the building name and manager are more important than the company logo.

```html
<!DOCTYPE html>
<html lang="en">
<head>
<meta charset="utf-8">
<title>Harborview Estates Business Card</title>
<link href="https://fonts.googleapis.com/css2?family=Oswald:wght@600&family=Roboto:wght@400;700&display=swap" rel="stylesheet">
<style>
  :root {
    --brand-blue: #1f5f9c;
    --link-blue: #3176b5;
    --ink: #1b1b1b;
    --grey: #959595;
    --charcoal: #3d4246;
    --paper: #ffffff;
    --backdrop: #e6e7e8;
  }
  * { margin: 0; padding: 0; box-sizing: border-box; }
  html, body { width: 1200px; height: 726px; overflow: hidden; }
  body {
    background: var(--backdrop);
    font-family: "Roboto", Arial, sans-serif;
    color: var(--ink);
    position: relative;
  }
  .card {
    position: absolute;
    top: 208px;
    width: 540px;
    height: 309px;
    background: var(--paper);
    box-shadow: 0 2px 10px rgba(0,0,0,0.12);
  }
  .card--front { left: 40px; }
  .card--back { left: 620px; }

  /* Front */
  .brand {
    position: absolute;
    left: 0; right: 0; top: 100px;
    display: flex;
    align-items: center;
    justify-content: center;
    gap: 14px;
  }
  .brand__dot {
    width: 46px; height: 46px;
    border-radius: 50%;
    background: var(--brand-blue);
  }
  .brand__name {
    font-weight: 700;
    font-size: 30px;
    letter-spacing: 1px;
    color: var(--brand-blue);
    line-height: 1;
  }
  .front-url {
    position: absolute;
    left: 0; right: 0; bottom: 52px;
    text-align: center;
    font-size: 15px;
    color: var(--ink);
  }
  .front-url span, .contact-list .web span { color: var(--link-blue); }

  /* Back */
  .manager {
    position: absolute;
    left: 40px; top: 86px;
  }
  .manager__name {
    font-family: "Oswald", "Arial Narrow", sans-serif;
    font-weight: 600;
    font-size: 34px;
    color: var(--brand-blue);
    line-height: 1;
    letter-spacing: 0.3px;
  }
  .manager__title {
    font-size: 20px;
    color: var(--ink);
    margin-top: 3px;
  }
  .address {
    position: absolute;
    left: 40px; top: 172px;
    font-size: 13px;
    line-height: 16px;
  }
  .contact-list {
    position: absolute;
    left: 40px; top: 214px;
    list-style: none;
    font-size: 13px;
  }
  .contact-list li {
    display: flex;
    align-items: center;
    gap: 9px;
    height: 17px;
  }
  .contact-list svg {
    width: 12px; height: 12px;
    fill: none;
    stroke: var(--brand-blue);
    stroke-width: 1.6;
  }
  .corner-brand {
    position: absolute;
    right: 32px; top: 32px;
    display: flex;
    align-items: center;
    gap: 8px;
  }
  .corner-brand .brand__dot { width: 26px; height: 26px; }
  .corner-brand .brand__name { font-size: 14px; letter-spacing: 0.5px; }
</style>
</head>
<body>

  <section class="card card--front" aria-label="Card front">
    <div class="brand">
      <div class="brand__dot"></div>
      <div class="brand__name">HARBORVIEW ESTATES LLC</div>
    </div>
    <p class="front-url">www.<span>harborviewestates</span>.us</p>
  </section>

  <section class="card card--back" aria-label="Card back">
    <div class="corner-brand">
      <div class="brand__dot"></div>
      <div class="brand__name">HARBORVIEW ESTATES</div>
    </div>

    <div class="manager">
      <h1 class="manager__name">DANA WHITLOW</h1>
      <p class="manager__title">Property Manager</p>
    </div>

    <address class="address" style="font-style:normal">
      2750 Larkspur Lane<br>
      #B210 Riverside, CA 92501
    </address>

    <ul class="contact-list">
      <li>
        <svg viewBox="0 0 12 12"><circle cx="6" cy="6" r="5"/><path d="M4 3.5l1 1.5-.6.7c.4.8 1 1.4 1.8 1.8l.7-.6 1.5 1-.6 1c-2.3-.3-4-2-4.4-4.4z"/></svg>
        555-302-4417
      </li>
      <li>
        <svg viewBox="0 0 12 12"><rect x="3" y="1.5" width="6" height="3"/><rect x="1" y="4.5" width="10" height="4.5" rx="1"/><rect x="3" y="7.5" width="6" height="3"/></svg>
        555-302-4480
      </li>
      <li>
        <svg viewBox="0 0 12 12"><rect x="1" y="2.5" width="10" height="7"/><path d="M1 2.5l5 4 5-4"/></svg>
        dana@harborviewestates.us
      </li>
      <li class="web">
        <svg viewBox="0 0 12 12"><circle cx="6" cy="6" r="5"/><ellipse cx="6" cy="6" rx="2" ry="5"/><path d="M1 6h10"/></svg>
        <p>www.<span>harborviewestates</span>.us</p>
      </li>
    </ul>
  </section>

</body>
</html>
```